We need a business card design, letterhead design and envelope design for our corporate image

We are looking for a corporate business card design, letterhead and envelope design to match the business card design. Logo is done.

```html
<!DOCTYPE html>
<html lang="en">
<head>
<meta charset="utf-8">
<title>Velcora Business Card</title>
<link href="https://fonts.googleapis.com/css2?family=Open+Sans:ital,wght@0,400;0,700;1,400&display=swap" rel="stylesheet">
<style>
  :root {
    --backdrop: #2b2b2d;
    --card-white: #ffffff;
    --slate: #6d6e71;
    --sun: #ffc60b;
    --ink: #58595b;
    --mark-light: #c4c5c8;
  }
  * { margin: 0; padding: 0; box-sizing: border-box; }
  html, body {
    width: 1200px; height: 900px; overflow: hidden;
    background: var(--backdrop);
    font-family: "Open Sans", Arial, sans-serif;
  }
  .canvas {
    position: relative; width: 1200px; height: 900px;
    display: flex; flex-direction: column; align-items: center; justify-content: center; gap: 24px;
  }
  .card {
    position: relative; width: 700px; height: 400px; overflow: hidden;
    box-shadow: 0 10px 30px rgba(0,0,0,.45);
  }
  .card-front { background: var(--card-white); }
  .card-back { background: var(--slate); display: flex; align-items: center; justify-content: center; }

  .front-wave { position: absolute; inset: 0; }

  .brand { display: flex; align-items: center; gap: 12px; }
  .brand-dot { border-radius: 50%; background: var(--sun); flex: none; }
  .brand-name { font-weight: 700; letter-spacing: -1px; line-height: 1; }

  .card-front .brand { position: absolute; left: 62px; top: 122px; }
  .card-front .brand-dot { width: 18px; height: 18px; }
  .card-front .brand-name { font-size: 56px; color: var(--ink); }

  .card-back .brand-dot { width: 26px; height: 26px; }
  .card-back .brand-name { font-size: 84px; color: var(--mark-light); }

  .divider { position: absolute; left: 372px; top: 86px; width: 2px; height: 148px; background: var(--sun); }

  .contact { position: absolute; left: 398px; top: 84px; color: var(--ink); font-size: 15px; line-height: 1.45; }
  .contact-name { color: var(--sun); font-weight: 700; font-size: 20px; letter-spacing: .5px; text-transform: uppercase; line-height: 1.2; }
  .contact-title { font-style: italic; font-size: 16px; margin-bottom: 10px; }
  .contact-line { display: flex; align-items: center; gap: 7px; }
  .contact-line svg { width: 13px; height: 13px; flex: none; }

  .website { position: absolute; left: 26px; top: 328px; color: #fff; font-style: italic; font-size: 15px; transform: rotate(14deg); transform-origin: left center; white-space: nowrap; }
</style>
</head>
<body>
<main class="canvas">
  <section class="card card-front">
    <svg class="front-wave" viewBox="0 0 700 400" preserveAspectRatio="none" aria-hidden="true">
      <path d="M0 248 C120 250 200 270 300 330 C400 390 520 392 700 390 L700 400 L0 400 Z" fill="var(--sun)"/>
      <path d="M0 262 C120 264 200 288 290 345 C380 400 520 402 660 400 L0 400 Z" fill="var(--slate)"/>
    </svg>
    <div class="brand">
      <span class="brand-dot"></span>
      <span class="brand-name">Velcora</span>
    </div>
    <div class="divider"></div>
    <div class="contact">
      <p class="contact-name">Dana Reyes</p>
      <p class="contact-title">President</p>
      <p>1820 Harbor View Lane</p>
      <p>Seacliff CA 90412</p>
      <p class="contact-line">
        <svg viewBox="0 0 16 16"><path d="M3 1l3 3-2 2c1 2 3 4 5 5l2-2 3 3-2 3C6 15 1 10 0 3z" fill="var(--sun)"/></svg>
        555-014-2278
      </p>
      <p class="contact-line">
        <svg viewBox="0 0 16 16"><rect x="1" y="3" width="14" height="10" fill="var(--sun)"/><path d="M1 3l7 6 7-6" fill="none" stroke="#fff" stroke-width="1.5"/></svg>
        dreyes@velcora.com
      </p>
    </div>
    <p class="website">www.velcora.com</p>
  </section>

  <section class="card card-back">
    <div class="brand">
      <span class="brand-dot"></span>
      <span class="brand-name">Velcora</span>
    </div>
  </section>
</main>
</body>
</html>
```